Wordpress Design Project

I have a main site www.tinymolarclinic.example for 9 dental offices. I want a designed wordpress mini-site template that I can use to create mini sites for each location and related projects that keeps the look and feel of the home site.
Updates

I'm getting different designs from my original web site. Maybe I'm confusing the designers but to clarify:

what I want is to keep the same graphics as we already have on this site www.tinymolarclinic.example and just convert it to a Wordpress site template to be used as individual MINI sites. 

No new designs needed, same design just different platform.

Target Market(s)

see site www.tinymolarclinic.example

Industry/Entity Type

Dental

Requirements
Must have
• Can we make the Logo larger?
Should not have
• I think you're basing your designs on tinymolarclinicglendale.example but I specifically said it should be based on the home site which is www.tinymolarclinic.example
Please view the difference. I need for it to have the same APPEARANCE. Please!
http://www.tinymolarclinic.example/

```html
<!DOCTYPE html>
<html lang="en">
<head>
<meta charset="utf-8">
<title>Tiny Molar Clinic</title>
<link rel="stylesheet" href="https://fonts.googleapis.com/css2?family=Source+Sans+3:ital,wght@0,400;0,600;0,700;1,600;1,700&family=Arimo:wght@400;700&display=swap">
<style>
:root{
  --page-top:#f6f6f7;
  --page-low:#e6e6e7;
  --ink:#4a4a4a;
  --ink-dark:#2f2f2f;
  --ink-soft:#666;
  --nav-blue:#2f7fd0;
  --nav-blue-light:#69b2ef;
  --badge-green:#7cb82b;
  --badge-green-dark:#4f8a15;
  --services-red:#c4123f;
  --appt-green:#4f9a14;
  --contact-purple:#7561b4;
  --panel-border:#f2c5cf;
  --card-red:#c8194a;
  --card-red-dark:#9e0f36;
  --divider:#b9c5d4;
  --brand-orange:#c2561f;
  --brand-dot:#e9a23b;
}
*{margin:0;padding:0;box-sizing:border-box}
html,body{width:1116px;height:1200px;overflow:hidden}
body{position:relative;font-family:"Source Sans 3",sans-serif;color:var(--ink);
  background:linear-gradient(var(--page-top) 0,var(--page-top) 729px,var(--page-low) 729px,var(--page-low) 100%)}
.abs{position:absolute}

.brand{left:140px;top:2px;width:112px;height:106px;display:flex;flex-direction:column;align-items:center;gap:3px}
.brand-dot{width:62px;height:62px;border-radius:50%;background:var(--brand-dot);flex:none}
.brand-name{font-weight:700;font-size:17px;line-height:18px;color:var(--brand-orange);text-align:center;white-space:nowrap}

.search{left:737px;top:5px;width:187px;height:38px;background:#fff;border-radius:8px;box-shadow:0 1px 4px rgba(0,0,0,.18);
  font-family:Arimo,sans-serif;font-size:11px;color:#777;padding:13px 0 0 16px}
.search-icon{left:935px;top:15px}

.nav{left:257px;top:53px;display:flex;align-items:center;gap:15px;font-size:13.5px;color:#444}
.nav-home{width:82px;height:29px;border-radius:15px;background:linear-gradient(var(--nav-blue-light),var(--nav-blue));
  color:#fff;font-weight:700;font-size:16px;display:flex;align-items:center;justify-content:center;margin-right:-6px;box-shadow:0 1px 3px rgba(0,0,0,.3)}

.badge{left:639px;top:97px;width:223px;height:58px;border-radius:14px 30px 14px 30px;
  background:linear-gradient(#a6d94a,var(--badge-green));border:2px solid var(--badge-green-dark);
  font-family:Arimo,sans-serif;font-size:12.5px;line-height:1.25;color:#173300;text-align:center;padding-top:10px;box-shadow:0 3px 5px rgba(0,0,0,.25)}

.hero-photo{left:118px;top:120px;width:440px;height:252px;border-radius:40px;
  background:radial-gradient(ellipse at 50% 55%,#d9b49a 0,#7d9ac7 45%,rgba(246,246,247,0) 72%)}
.mission{left:554px;top:168px;font-weight:700;font-style:italic;font-size:41px;line-height:44px;color:#4a4a4a;letter-spacing:-.6px;text-shadow:0 2px 2px rgba(0,0,0,.15)}
.mission-sub{left:558px;top:262px;width:400px;font-size:18.5px;line-height:22px;color:#555}
.slider-dots{left:520px;top:393px;display:flex;gap:5px}
.slider-dots span{width:13px;height:13px;border-radius:50%;background:#ddd;border:1px solid #aaa}
.slider-dots .on{background:#444}

.info-panel{left:146px;top:424px;width:812px;height:291px;border:3px solid var(--panel-border);border-radius:16px;
  background:rgba(255,255,255,.55);box-shadow:0 0 8px rgba(230,140,160,.35)}
.col-title{top:440px;font-weight:700;font-style:italic;font-size:26px}
.col-services{left:209px;color:var(--services-red)}
.col-appt{left:485px;color:var(--appt-green)}
.col-contact{left:756px;color:var(--contact-purple)}
.divider{top:478px;width:1px;height:192px;background:var(--divider)}
.service-list{left:170px;top:483px;list-style:none;font-weight:700;font-size:16px;line-height:19.4px;color:#3a3a3a}
.service-list li::before{content:"• "}
.appt-text{left:444px;top:481px;width:232px;font-size:13px;line-height:27px;color:#333}
.contact-text{left:707px;top:482px;font-weight:700;font-size:16px;line-height:19.5px;color:#3a3a3a}
.contact-text p+p{margin-top:20px}

.beautify{left:155px;top:730px;font-size:40px;font-weight:400;color:#555;letter-spacing:-.8px}
.beautify b{font-style:italic;font-weight:700}
.services-heading{left:167px;top:770px;font-weight:700;font-style:italic;font-size:24px;color:#4a4a4a}
.small-list{left:167px;top:802px;list-style:none;font-size:12px;line-height:18px;color:#555}
.small-list li::before{content:"• "}
.body-copy{left:167px;width:622px;font-size:11.5px;line-height:18.6px;color:#555}

.serve-card{left:673px;top:759px;width:282px;height:226px;background:linear-gradient(160deg,#d42a5a,var(--card-red));
  box-shadow:0 6px 10px rgba(0,0,0,.2);clip-path:polygon(0 0,86% 0,100% 14%,100% 100%,4% 100%,0 88%)}
.serve-title{left:688px;top:774px;font-weight:700;font-size:23px;color:#fff;letter-spacing:-.3px}
.serve-text{left:688px;top:818px;width:240px;font-family:Arimo,sans-serif;font-size:18.5px;line-height:24px;color:#fff;word-break:break-all}
.read-more{left:810px;top:932px;width:150px;height:34px;background:linear-gradient(#e0416f,var(--card-red-dark));
  color:#fff;font-weight:700;font-size:19px;display:flex;align-items:center;justify-content:center;border-radius:3px;box-shadow:0 2px 3px rgba(0,0,0,.3)}
</style>
</head>
<body>

<div class="abs brand"><span class="brand-dot"></span><span class="brand-name">Tiny Molar<br>Clinic</span></div>

<nav class="abs nav">
  <span class="nav-home">Home</span>
  <span>About Us</span><span>Services</span><span>Gallery</span><span>Appointment</span><span>Promise</span>
  <span>Patient Log In</span><span>Locations</span><span>Blog</span><span>FAQ's</span><span>Contact Us</span>
</nav>

<div class="abs search">search this site...</div>
<svg class="abs search-icon" width="16" height="16" viewBox="0 0 16 16" aria-hidden="true">
  <circle cx="9" cy="6" r="4.5" fill="none" stroke="#999" stroke-width="1.5"/><line x1="6" y1="9.5" x2="2" y2="14" stroke="#999" stroke-width="1.8"/>
</svg>

<div class="abs badge">Now taking appointments for<br>Our Second location at Brookfield</div>

<div class="abs hero-photo" role="img" aria-label="Three smiling children playfully piled on top of each other"></div>
<h1 class="abs mission">Our mission is to bring<br>smiles for kids.</h1>
<p class="abs mission-sub">That we treat Smiles that are healthy, individually beautiful yet a universal language that everyone understands.</p>
<div class="abs slider-dots"><span></span><span></span><span class="on"></span><span></span><span></span><span></span></div>

<div class="abs info-panel"></div>
<h2 class="abs col-title col-services">Our Services.</h2>
<h2 class="abs col-title col-appt">Appointment.</h2>
<h2 class="abs col-title col-contact">Contact Us.</h2>
<span class="abs divider" style="left:415px"></span>
<span class="abs divider" style="left:686px"></span>
<ul class="abs service-list">
  <li>Cleaning/Flouride Treatment</li><li>Preventive Care</li><li>Pedo Partial</li><li>Extractions</li>
  <li>Amalgam Fillings</li><li>Composite Fillings</li><li>Space Maintainers</li><li>Kinder Crowns</li>
  <li>Pulpotomies</li><li>Sealants</li><li>Orthodontics</li>
</ul>
<p class="abs appt-text">Tiny Molar Clinic accepts all private insurances, StateDent &amp; all major credit cards, Financial assistance may be arranged for those with financial need. At Tiny Molar Clinic, we are your servants providing the highest quality dental care to you and your loved ones.</p>
<div class="abs contact-text">
  <p>1820 Maple Grove Ave.<br>Pasadena, CA 91101</p>
  <p>maple@tinymolarclinic.example</p>
  <p>(555) 014-2210 Office<br>(555) 014-2288 fax</p>
</div>

<h2 class="abs beautify"><b>beautify</b> your Smiles...</h2>
<h3 class="abs services-heading">The Services are:</h3>
<ul class="abs small-list">
  <li>Cleaning/Flouride Treatment</li><li>Preventive Care</li><li>Pedo Partial</li><li>Extractions</li>
  <li>Amalgam Fillings</li><li>Composite Fillings</li><li>Space Maintainers</li><li>Kinder Crowns</li>
  <li>Pulpotomies</li><li>Sealants</li><li>Orthodontics</li><li>Thumb Sucking Appliance</li>
</ul>
<p class="abs body-copy" style="top:1036px">Tiny Molar Clinic uses only, the State of the art equipment known in the industry. By using the Digitally based equipment Tiny Molar Clinic has seen vast improvement in efficiency, and overall quality of care that we can deliver to our clients. We also understand the importance of keeping our ecosystem and environment healthy so we are retro-fitting all of our offices to go paperless. "Go Green"</p>
<p class="abs body-copy" style="top:1125px">Tiny Molar Clinic accepts all private insurances, StateDent &amp; all major credit cards, Financial assistance may be arranged for those with financial need. At Tiny Molar Clinic, we are your servants providing the highest quality dental care to you and your loved ones.</p>

<div class="abs serve-card"></div>
<div class="abs serve-title">OFFICE TO SERVE YOU.</div>
<p class="abs serve-text">Look and Click Below for the Office to Serve you. customerservice@tinymolarclinic.example</p>
<div class="abs read-more">Read more</div>

</body>
</html>
```